Modern card design needed for building development company

We are looking for a sharp modern new look for our business cards.
We are a New Zealand based company called TKR Ventures NZ LTD that specialises in subdividing large sections, housing and commercial buildings.
We have attached a photo of the current logo and would like to see it improved somehow as it looks a bit dated.
We are open to any colours.

Target Market(s)

Investors, Property buyers

Industry/Entity Type

Investment

Contact Information for Business Card

TKR VENTURES NZ LTD
www.tkrventuresnz.co.nz

Damon Whitcombe
Phone +64 21 938 104
Email dpwhitcombe@korumail.co.nz

Font styles to use
Serif
Sans Serif

Colors
0792cd
33a6d7
85cae6
6b449b
886aae
f04a50
ec1f27
f37122
f68d4d

Requirements
Must have
• Please try and make the logo more modern or if you have a similar one we would like to see it.

```html
<!DOCTYPE html>
<html lang="en">
<head>
<meta charset="utf-8">
<title>TKR Ventures NZ LTD – Business Card</title>
<link href="https://fonts.googleapis.com/css2?family=Montserrat:wght@600;700&family=Work+Sans:wght@300;400&display=swap" rel="stylesheet">
<style>
  :root {
    --brand-red: #8c1727;
    --ink: #2b2b2b;
    --rule: #333333;
    --paper: #ffffff;
    --backdrop: #e9e6e2;
  }
  * { box-sizing: border-box; margin: 0; padding: 0; }
  html, body { width: 1200px; height: 930px; overflow: hidden; }
  body { background: var(--backdrop); position: relative; font-family: "Work Sans", sans-serif; color: var(--ink); }

  .card { position: absolute; left: 278px; width: 644px; height: 369px; overflow: hidden; }
  .card--front { top: 75px; background: var(--paper); }
  .card--back { top: 486px; background: var(--brand-red); }

  .brand { position: absolute; display: flex; align-items: center; gap: 10px;
    font-family: "Montserrat", sans-serif; font-weight: 600; letter-spacing: 2px; }
  .brand__mark { width: 14px; height: 14px; }
  .card--front .brand { left: 33px; top: 100px; font-size: 16px; color: var(--brand-red); }
  .card--front .brand__mark { background: var(--brand-red); }
  .card--back .brand { left: 0; right: 0; top: 170px; justify-content: center; font-size: 20px; color: var(--paper); }
  .card--back .brand__mark { background: var(--paper); }

  .person { position: absolute; right: 32px; top: 186px; text-align: right; }
  .person__name { font-family: "Montserrat", sans-serif; font-weight: 700; font-size: 23px; color: var(--brand-red); letter-spacing: 0.3px; line-height: 1; }
  .person__role { font-size: 16px; font-weight: 400; margin-top: 4px; }

  .divider { position: absolute; left: 33px; right: 32px; top: 257px; height: 1px; background: var(--rule); }

  .contacts { position: absolute; left: 33px; top: 275px; list-style: none; }
  .contacts li { display: flex; align-items: center; height: 20px; font-size: 16px; font-weight: 300; }
  .contacts svg { width: 10px; height: 10px; margin: 0 13px 0 1px; }

  .address { position: absolute; right: 32px; top: 295px; text-align: right; font-size: 16px; font-weight: 300; line-height: 20px; }

  .footer-band { position: absolute; left: 0; bottom: 0; width: 644px; height: 28px; }
</style>
</head>
<body>
  <section class="card card--front">
    <div class="brand"><span class="brand__mark"></span>TKR VENTURES NZ LTD</div>

    <div class="person">
      <h1 class="person__name">DAMON WHITCOMBE</h1>
      <p class="person__role">Director</p>
    </div>

    <div class="divider"></div>

    <ul class="contacts">
      <li><svg viewBox="0 0 10 10" aria-hidden="true"><path d="M2 0.5 L3.6 2.8 L2.8 3.8 Q4 6.4 6.2 7.2 L7.2 6.4 L9.5 8 L8.4 9.5 Q2.5 8.5 0.5 1.6 Z" fill="none" stroke="#2b2b2b" stroke-width="1"/></svg>+64 21 938 104</li>
      <li><svg viewBox="0 0 10 10" aria-hidden="true"><rect x="0.5" y="2" width="9" height="6.5" fill="none" stroke="#2b2b2b" stroke-width="1"/><path d="M0.5 2 L5 5.5 L9.5 2" fill="none" stroke="#2b2b2b" stroke-width="1"/></svg>dpwhitcombe@korumail.co.nz</li>
      <li><svg viewBox="0 0 10 10" aria-hidden="true"><circle cx="5" cy="5" r="4.5" fill="none" stroke="#2b2b2b" stroke-width="0.9"/><ellipse cx="5" cy="5" rx="2" ry="4.5" fill="none" stroke="#2b2b2b" stroke-width="0.9"/><path d="M0.5 5 H9.5" stroke="#2b2b2b" stroke-width="0.9"/></svg>www.tkrventuresnz.co.nz</li>
    </ul>

    <address class="address" style="font-style:normal">PO BOX 48215 Devonport<br>Auckland New Zealand</address>

    <svg class="footer-band" viewBox="0 0 644 28" aria-hidden="true">
      <path d="M0 17 H600 V28 H0 Z" fill="var(--brand-red)"/>
      <path d="M0 7 H370 Q380 7 388 11 L390 12 Q380 14 366 14 H0 Z" fill="#222"/>
      <path d="M364 17 Q385 14 410 5 Q422 0 440 0 H644 V28 H364 Z" fill="var(--brand-red)"/>
    </svg>
  </section>

  <section class="card card--back">
    <div class="brand"><span class="brand__mark"></span>TKR VENTURES NZ LTD</div>
  </section>
</body>
</html>
```